Oriel Photography Business Card

I need a business card designed for a photography business based in Perth, Western Australia called Oriel Photography.

We specialise in wedding, event photography and portrait photography.

The business card must borrow the style of the attached logo.

The hex codes for the colours in the logo are:
#ED1D85 - Pink
#89C23E - Green
#37282F - Black

The name on the card will be:
Name: Tobrian
Phone: 0417395268
Website: www.orielphotography.example.com.au
Facebook: orielphotography

I am open and happy to accept creative concepts.

I’d like some space at the back for writing notes and appointment details.

```html
<!DOCTYPE html>
<html lang="en">
<head>
<meta charset="utf-8">
<title>Oriel Photography – Business Card</title>
<link rel="stylesheet" href="https://fonts.googleapis.com/css2?family=Cinzel:wght@400&family=Source+Sans+3:ital,wght@0,300;0,400;0,600;0,700;1,400&display=swap">
<style>
  :root {
    --pink: #ED1D85;
    --green: #89C23E;
    --ink: #37282F;
    --grey: #5a5a5a;
    --soft-grey: #8a8a8a;
    --rule: #b9b9b9;
    --paper: #ffffff;
    --backdrop: #ece8e3;
  }
  * { box-sizing: border-box; margin: 0; padding: 0; }
  html, body { width: 1200px; height: 720px; overflow: hidden; }
  body {
    background: var(--backdrop);
    font-family: "Source Sans 3", "Helvetica Neue", Arial, sans-serif;
    color: var(--grey);
  }
  .sheet {
    position: relative;
    width: 1200px; height: 720px;
    display: flex; align-items: center; justify-content: center; gap: 40px;
  }
  .card {
    position: relative;
    width: 540px; height: 330px;
    background: var(--paper);
    overflow: hidden;
    box-shadow: 0 2px 3px rgba(0,0,0,.08), 0 10px 24px rgba(0,0,0,.12);
  }

  /* ---------- Front ---------- */
  .card-front .header-band { position: absolute; inset: 0 0 auto 0; }
  .brand-name {
    position: absolute; left: 0; right: 0; top: 172px;
    text-align: center;
    font-weight: 300; font-size: 17px;
    letter-spacing: .62em; text-indent: .62em;
    color: var(--grey);
    text-transform: uppercase;
  }
  .contact {
    position: absolute; top: 222px; left: 0; right: 0;
    display: flex; justify-content: center; align-items: stretch;
  }
  .contact-person { text-align: right; padding-right: 14px; }
  .person-name {
    color: var(--pink); font-weight: 700; font-size: 20px;
    letter-spacing: .03em; text-transform: uppercase; line-height: 1.2;
  }
  .contact-line {
    display: flex; align-items: center; gap: 6px;
    font-size: 14px; color: var(--ink); line-height: 1.5;
  }
  .contact-person .contact-line { justify-content: flex-end; }
  .divider { width: 1px; background: var(--rule); margin: 2px 0; }
  .contact-online { padding-left: 14px; padding-top: 2px; }
  .contact-online .contact-line { font-size: 13px; }
  .icon { flex: none; }

  /* ---------- Back ---------- */
  .card-back .faint-mark {
    position: absolute; left: 195px; top: 60px;
    width: 170px; height: 200px; border-radius: 50%;
    background: radial-gradient(ellipse at center, rgba(137,194,62,.10) 0%, rgba(237,29,133,.10) 45%, rgba(237,29,133,0) 72%);
  }
  .appointment-title {
    position: absolute; top: 26px; left: 0; right: 0; text-align: center;
    font-family: "Cinzel", "Times New Roman", serif;
    color: var(--pink); font-size: 20px; letter-spacing: .06em;
  }
  .field {
    position: absolute; display: flex; align-items: flex-end; gap: 8px;
    font-size: 15px; color: var(--grey);
  }
  .field-label { white-space: nowrap; }
  .dotted-line { flex: 1; border-bottom: 1px dotted var(--soft-grey); height: 1px; margin-bottom: 5px; }
  .write-box {
    width: 100px; height: 22px;
    border: 1px solid var(--soft-grey); border-radius: 2px; background: rgba(255,255,255,.7);
  }
  .tick-box {
    width: 24px; height: 20px;
    border: 1px solid var(--soft-grey); border-radius: 2px; background: rgba(255,255,255,.7);
  }
  .field-name { left: 40px; right: 40px; top: 78px; }
  .field-date { left: 40px; width: 240px; top: 128px; }
  .field-time { left: 300px; top: 124px; align-items: center; }
  .ampm { font-size: 14px; }
  .field-next { left: 40px; right: 40px; top: 176px; align-items: center; }
  .day-row {
    position: absolute; left: 40px; right: 40px; top: 226px;
    display: flex; justify-content: space-between; align-items: center;
  }
  .day { display: flex; align-items: center; gap: 6px; font-weight: 600; font-size: 14px; color: var(--grey); }
  .cancellation-note {
    position: absolute; left: 0; right: 0; top: 276px; text-align: center;
    font-style: italic; font-size: 15px; color: var(--soft-grey);
  }
</style>
</head>
<body>
<main class="sheet">

  <!-- Front of card -->
  <section class="card card-front" aria-label="Business card front">
    <svg class="header-band" width="540" height="170" viewBox="0 0 540 170" aria-hidden="true">
      <rect x="0" y="0" width="540" height="118" fill="var(--pink)"/>
      <rect x="0" y="122" width="540" height="2" fill="var(--green)"/>
      <circle cx="270" cy="96" r="66" fill="var(--paper)"/>
      <circle cx="270" cy="96" r="30" fill="var(--pink)"/>
    </svg>

    <p class="brand-name">Oriel Photography</p>

    <div class="contact">
      <div class="contact-person">
        <p class="person-name">Tobrian</p>
        <p class="contact-line">
          <svg class="icon" width="13" height="13" viewBox="0 0 14 14" aria-hidden="true">
            <circle cx="7" cy="7" r="6.3" fill="none" stroke="var(--pink)" stroke-width="1.4"/>
            <path d="M5 3.8c-.6.3-1 .9-.9 1.7.3 2 1.9 3.9 3.9 4.5.8.2 1.5-.1 1.9-.7l-1.2-1-.8.5c-.9-.4-1.6-1.2-2-2.1l.5-.8z" fill="var(--pink)"/>
          </svg>
          0417395268
        </p>
      </div>
      <span class="divider" aria-hidden="true"></span>
      <div class="contact-online">
        <p class="contact-line">
          <svg class="icon" width="11" height="11" aria-hidden="true"><rect width="11" height="11" rx="1.5" fill="var(--pink)"/></svg>
          orielphotography
        </p>
        <p class="contact-line">
          <svg class="icon" width="11" height="11" aria-hidden="true"><circle cx="5.5" cy="5.5" r="5.5" fill="var(--pink)"/></svg>
          www.orielphotography.example.com.au
        </p>
      </div>
    </div>
  </section>

  <!-- Back of card -->
  <section class="card card-back" aria-label="Business card back – appointment details">
    <div class="faint-mark" role="img" aria-label="Faint brand emblem in soft pink and green"></div>

    <h1 class="appointment-title">Your Appointment</h1>

    <div class="field field-name">
      <span class="field-label">Name :</span><span class="dotted-line"></span>
    </div>
    <div class="field field-date">
      <span class="field-label">Date :</span><span class="dotted-line"></span>
    </div>
    <div class="field field-time">
      <span class="field-label">Time :</span><span class="write-box"></span><span class="ampm">am / pm</span>
    </div>
    <div class="field field-next">
      <span class="field-label">Next Appointment</span><span class="dotted-line"></span>
    </div>

    <div class="day-row">
      <span class="day">MON <span class="tick-box"></span></span>
      <span class="day">TUE <span class="tick-box"></span></span>
      <span class="day">WED <span class="tick-box"></span></span>
      <span class="day">THU <span class="tick-box"></span></span>
      <span class="day">FRI <span class="tick-box"></span></span>
      <span class="day">SAT <span class="tick-box"></span></span>
    </div>

    <p class="cancellation-note">We appreciate a 24 hr. notice for cancellations</p>
  </section>

</main>
</body>
</html>
```